BRAMBLEFORD CONSTRUCTIONS B-Card

I currently have a b-card design but will be removing the image (tree) from the logo and have text only.
I want the card to be classy and strong within the building and construction industry.
I will be using Spot UV on the cards as per the attached examples. I will also send through some sketched ideas that I have in mind.
The color blue is similar to the image (No. 6) attached images

Target Market(s)

middle to maturre aged.
Home Owners / Renovators and Builders

Industry/Entity Type

Construction

Contact Information for Business Card

BRAMBLEFORD CONSTRUCTIONS
Name: Gareth Pennick
Title: Project Manager
Mobile: 0427 351 804
Office: (08) 9316 5172
Address: 47C Corvell Street, Malaga WA 6090
Email: info@bramblefordhomes.com.au
PO Box: 3817 Malaga WA 6944

Colors
0592cd
33a6d7
85cae6
1b1b1b

Requirements
Must have
• 1. It must have spot UV on the front of card, maybe back of card too
• 2. I really like the blue on image 6. (or at least a really cool electric blue against the charcoal grey background)
• 3. The font must be slimline and modern. Easy to read
• 4. There must be no black used on the card... Only greys and dark charcoal greys
• 5. Use only the text from the logo "Brambleford Constructions" Not the image of the tree. I am wanting the b-cards to be more masculine.
Nice to have
• 1. I like the design concept on image 6. but happy to see what else you can do with the Spot UV
• 2. Unless you have a really cool idea of the image of the tree (from previous logo) Spot UV somewhere in the design concept thats original and different then I am keen to see what you come up with
• 3. Try changing the color of the logo eg. full white or Blue and white
• 4. Another option is to have the Brambleford Logo on the front of card with the spot UV in the background of text which we specialise in eg, Roofing, Ceiling, Insulation, Gutter Guards, Electrical, Insurance etc and we can add or reduce items as required. Similar to image 12.
Should not have
• Do not include the image of the tree from previous logo. unless you have a really cool idea of Spot UV somewhere in the design concept thats original and different.

```html
<!DOCTYPE html>
<html lang="en">
<head>
<meta charset="utf-8">
<title>Brambleford Constructions – Business Card</title>
<link rel="stylesheet" href="https://fonts.googleapis.com/css2?family=Jost:wght@400;500;600&display=swap">
<style>
  :root {
    --brand-blue: #1b5aa7;
    --brand-blue-dark: #16509a;
    --card-white: #ffffff;
    --text-grey: #4a4a4a;
    --title-grey: #2f2f2f;
    --sub-grey: #3a3a3a;
    --name-blue: #1d5aa3;
    --divider: #b9b9b9;
    --backdrop: #5b4a3b;
  }
  * { margin: 0; padding: 0; box-sizing: border-box; }
  html, body { width: 1200px; height: 987px; overflow: hidden; }
  body {
    background: var(--backdrop);
    font-family: "Jost", sans-serif;
    position: relative;
  }
  .card {
    position: absolute;
    left: 300px;
    width: 609px;
    height: 349px;
  }
  /* Front */
  .card--front { top: 156px; background: var(--brand-blue); }
  .card--front .card__face {
    position: absolute;
    left: 13px; top: 14px; right: 14px; bottom: 13px;
    background: var(--card-white);
  }
  .wordmark { position: absolute; text-align: center; font-weight: 500; line-height: 1; }
  .wordmark__name { display: block; }
  .wordmark__sub { display: block; }
  .card--front .wordmark {
    left: 28px; width: 260px; top: 124px; color: var(--brand-blue);
  }
  .card--front .wordmark__name { font-size: 33px; }
  .card--front .wordmark__sub { font-size: 13.5px; letter-spacing: 5.3px; margin-top: 7px; color: var(--sub-grey); }
  .divider {
    position: absolute; left: 299px; top: 47px; width: 1px; height: 234px;
    background: linear-gradient(to bottom, transparent, var(--divider) 15%, var(--divider) 85%, transparent);
  }
  .contact { position: absolute; left: 323px; top: 56px; color: var(--text-grey); }
  .contact__name { font-size: 24px; font-weight: 600; color: var(--name-blue); line-height: 1.2; }
  .contact__title { font-size: 18px; font-weight: 400; color: var(--title-grey); margin-top: 1px; }
  .contact__address { font-size: 16.5px; line-height: 20px; margin-top: 13px; }
  .contact__lines { list-style: none; margin-top: 7px; }
  .contact__lines li { display: flex; align-items: center; font-size: 16.5px; height: 23px; }
  .contact__lines li.email { font-size: 15px; }
  .contact__lines svg { width: 14px; height: 14px; margin-right: 8px; fill: var(--name-blue); flex: none; }

  /* Back */
  .card--back { top: 527px; background: var(--card-white); }
  .card--back .card__face {
    position: absolute;
    left: 12px; top: 13px; right: 13px; bottom: 12px;
    background: var(--brand-blue-dark);
  }
  .card--back .wordmark { left: 0; right: 0; top: 138px; color: var(--card-white); }
  .card--back .wordmark__name { font-size: 48px; }
  .card--back .wordmark__sub { font-size: 19px; letter-spacing: 7.5px; margin-top: 9px; }
  .services {
    position: absolute; left: 0; right: 0; top: 268px;
    text-align: center; color: var(--card-white);
    font-size: 16.5px; line-height: 22px; font-weight: 400;
  }
</style>
</head>
<body>
  <section class="card card--front" aria-label="Business card front">
    <div class="card__face">
      <div class="wordmark">
        <span class="wordmark__name">BRAMBLEFORD</span>
        <span class="wordmark__sub">CONSTRUCTIONS</span>
      </div>
      <div class="divider"></div>
      <div class="contact">
        <p class="contact__name">Gareth Pennick</p>
        <p class="contact__title">Project Manager</p>
        <p class="contact__address">47C Corvell Street<br>Harrowby WA 6071<br>PO Box:3817 Harrowby<br>WA 6958</p>
        <ul class="contact__lines">
          <li><svg viewBox="0 0 24 24" aria-hidden="true"><path d="M6.6 10.8c1.4 2.8 3.8 5.1 6.6 6.6l2.2-2.2c.3-.3.7-.4 1-.2 1.1.4 2.3.6 3.6.6.6 0 1 .4 1 1V20c0 .6-.4 1-1 1C10.6 21 3 13.4 3 4c0-.6.4-1 1-1h3.5c.6 0 1 .4 1 1 0 1.3.2 2.5.6 3.6.1.3 0 .7-.2 1z"/></svg>(08) 9316 5172</li>
          <li><svg viewBox="0 0 24 24" aria-hidden="true"><path d="M7 1h10a2 2 0 0 1 2 2v18a2 2 0 0 1-2 2H7a2 2 0 0 1-2-2V3a2 2 0 0 1 2-2zm0 3v14h10V4zm5 15.5a1 1 0 1 0 0 2 1 1 0 0 0 0-2z"/></svg>0427 351 804</li>
          <li class="email"><svg viewBox="0 0 24 24" aria-hidden="true"><path d="M2 5h20v14H2zm2 2v.5l8 5 8-5V7zm0 2.8V17h16V9.8l-8 5z"/></svg>info@bramblefordhomes.com.au</li>
        </ul>
      </div>
    </div>
  </section>

  <section class="card card--back" aria-label="Business card back">
    <div class="card__face" role="img" aria-label="Blue background with a faint tonal spot UV name pattern"></div>
    <div class="wordmark">
      <span class="wordmark__name">BRAMBLEFORD</span>
      <span class="wordmark__sub">CONSTRUCTIONS</span>
    </div>
    <p class="services">Roofing | Ceiling | Insulation | Gutter Guards<br>Electrical | Insurance etc</p>
  </section>
</body>
</html>
```